Premium CBD/Hemp company needs packaging and label design

Quillmore Apothecare, a premium CBD/Hemp company based in Scottsdale, Arizona is in need of a packaging and label design. We are launching with our flagship product which will be a 30 count capsule and will come in three functions: Pain Relief, Anxiety Support, and Sleep Support. For the purpose of this contest, please design packaging and label for our Anxiety Support product. Our products are physician formulated and all natural. Our main ingredient is CBD/Hemp and is complemented by specific herbs that synergistically work together to give the customer the most effective and desired result. We would like our branding to have a pharmaceutical look and feel with a focus on trust and transparency. We have uploaded our company logo that is to be used on both the packaging and label. We have also uploaded an executed branding questionnaire that will guide you to exactly what we are seeking to achieve as to the look and feel of our brand. Please feel free to contact us with any questions that you may have. The winner of this contest will have the opportunity to work with us on future projects as we will need packaging and label design for our entire Quillmore Apothecare product line.

Target Market(s)

See attached branding questionnaire

Industry/Entity Type

Health And Wellness

Font styles to use
Sans Serif

Colors

Designer to choose colors to be used in the design.

Requirements
Must have
• See attached branding questionnaire; Please superimpose labels onto a cobalt blue capsule bottle (see attached)
• >>UPON REVIEW of the FIRST 8 designs, we really like the silver, mildly metallic label background in DESIGN # 21300528, we do not want metalic lettering as that would not look very "Pharmaceutical"
• >>We are in search of a look that is a bit more "Pharmaceutical" than a look that would be more commonly found in a Supplement Store
Nice to have
• "See attached branding questionnaire
Should not have
• See attached branding questionnaire; NO marijuana or cannabis plant on the packaging or label

```html
<!DOCTYPE html>
<html lang="en">
<head>
<meta charset="utf-8">
<title>Quillmore Apothecare – Hemp Extract Packaging</title>
<link href="https://fonts.googleapis.com/css2?family=Montserrat:wght@500;600;700;800&family=Roboto+Condensed:wght@400&family=Open+Sans:wght@400&display=swap" rel="stylesheet">
<style>
  :root{
    --bg:#eceeef;
    --navy:#16239a;
    --navy-dark:#0e1870;
    --green:#13a04a;
    --green-dark:#0b8a3a;
    --green-text:#10913f;
    --white:#ffffff;
    --silver-light:#f7f8f9;
    --silver:#dfe2e5;
    --silver-dark:#b9bec4;
    --ink:#1f1f1f;
    --grey-text:#444a50;
  }
  *{margin:0;padding:0;box-sizing:border-box}
  html,body{width:1200px;height:1200px;overflow:hidden;background:var(--bg)}
  body{position:relative;font-family:"Montserrat",sans-serif}

  .carton{position:absolute;left:180px;top:100px;width:840px;height:1000px;display:flex}
  .panel{position:relative;height:100%;overflow:hidden;background:linear-gradient(180deg,var(--silver-light),var(--silver))}
  .panel--side{width:300px;border-right:1px solid var(--silver-dark)}
  .panel--front{width:540px}

  .band-top{position:absolute;left:0;top:0;width:100%;height:14px;background:var(--navy)}
  .band-bottom{position:absolute;left:0;bottom:0;width:100%;height:30px;background:var(--navy)}
  .leaf-field{position:absolute;left:0;top:14px;width:100%;height:556px;
    background:linear-gradient(160deg,var(--green) 0%,var(--green-dark) 100%)}

  /* side panel */
  .side-title{position:absolute;left:150px;top:290px;transform:translate(-50%,-50%) rotate(-90deg);
    white-space:nowrap;color:var(--white);text-align:left}
  .side-title__main{font-weight:800;font-size:46px;line-height:44px;letter-spacing:1px}
  .side-title__sub{font-weight:500;font-size:13px;letter-spacing:6px;margin-top:8px}
  .side-copy{position:absolute;left:34px;top:640px;width:230px;font-family:"Open Sans",sans-serif;
    font-size:15px;line-height:27px;color:var(--grey-text);text-align:justify}

  /* front panel */
  .brand-tab{position:absolute;left:40px;top:0;width:460px;height:170px}
  .brand{position:absolute;left:90px;top:54px;width:360px;display:flex;align-items:center;gap:18px}
  .brand__dot{width:62px;height:62px;border-radius:50%;background:var(--white);flex:none}
  .brand__name{color:var(--white);font-weight:600;font-size:30px;line-height:34px;letter-spacing:1px}

  .product-title{position:absolute;left:0;top:240px;width:100%;text-align:center;color:var(--white)}
  .product-title__main{font-weight:800;font-size:100px;line-height:104px;letter-spacing:-1px}
  .product-title__sub{font-weight:600;font-size:24px;letter-spacing:10px;margin-top:16px}

  .seal{position:absolute;left:50%;top:500px;width:140px;height:140px;margin-left:-70px;border-radius:50%;
    background:var(--navy);box-shadow:0 0 0 6px var(--silver),0 0 0 8px var(--silver-dark)}
  .seal::after{content:"";position:absolute;inset:14px;border-radius:50%;border:2px solid var(--white)}

  .benefits{position:absolute;left:60px;top:690px;width:420px;display:flex;justify-content:space-between}
  .benefit{width:120px;display:flex;flex-direction:column;align-items:center}
  .benefit__icon{width:84px;height:84px;border-radius:50%;
    background:radial-gradient(circle at 35% 30%,var(--white),var(--silver) 60%,var(--silver-dark));
    display:flex;align-items:center;justify-content:center;box-shadow:0 4px 8px rgba(0,0,0,.15)}
  .benefit__label{font-family:"Roboto Condensed",sans-serif;font-size:19px;line-height:24px;color:var(--ink);
    text-align:center;margin-top:16px;text-transform:uppercase}

  .strength{position:absolute;left:40px;top:870px;color:var(--ink)}
  .strength__dose{font-weight:700;font-size:32px;letter-spacing:-1px}
  .strength__dose small{font-size:16px;font-weight:600}
  .strength__cbd{font-weight:800;font-size:64px;line-height:60px;color:var(--green-text)}

  .count-tab{position:absolute;right:0;top:870px;width:300px;height:100px}
  .count{position:absolute;right:24px;top:892px;display:flex;align-items:center;gap:14px;color:var(--ink)}
  .count__num{font-weight:800;font-size:34px;letter-spacing:-1px}
  .count__num small{font-size:22px;font-weight:700;letter-spacing:0}
</style>
</head>
<body>
<main class="carton">

  <section class="panel panel--side">
    <div class="band-top"></div>
    <div class="leaf-field" role="img" aria-label="Green leaf pattern background"></div>
    <div class="side-title">
      <div class="side-title__main">HEMP<br>EXTRACT</div>
      <div class="side-title__sub">FULL SPECTRUM</div>
    </div>
    <p class="side-copy">Physician formulated blend of full spectrum hemp extract and select herbs. Take one capsule daily with water, or as directed by your physician. Store in a cool, dry place away from sunlight.</p>
    <div class="band-bottom"></div>
  </section>

  <section class="panel panel--front">
    <div class="band-top"></div>
    <div class="leaf-field" role="img" aria-label="Green leaf pattern background"></div>

    <svg class="brand-tab" viewBox="0 0 460 170" aria-hidden="true">
      <polygon points="4,0 456,0 456,118 440,160 20,160 4,118" fill="#c9cdd2"/>
      <polygon points="14,0 446,0 446,114 432,150 28,150 14,114" fill="#16239a"/>
    </svg>
    <div class="brand">
      <span class="brand__dot"></span>
      <span class="brand__name">QUILLMORE<br>APOTHECARE</span>
    </div>

    <div class="product-title">
      <div class="product-title__main">HEMP<br>EXTRACT</div>
      <div class="product-title__sub">FULL SPECTRUM</div>
    </div>

    <div class="seal" role="img" aria-label="Quality seal"></div>

    <ul class="benefits" style="list-style:none">
      <li class="benefit">
        <span class="benefit__icon">
          <svg width="44" height="44" viewBox="0 0 44 44" fill="none" stroke="#13a04a" stroke-width="3">
            <circle cx="22" cy="22" r="18"/><circle cx="22" cy="22" r="8" fill="#13a04a"/><line x1="8" y1="8" x2="36" y2="36"/>
          </svg>
        </span>
        <span class="benefit__label">Pain Relief</span>
      </li>
      <li class="benefit">
        <span class="benefit__icon">
          <svg width="44" height="44" viewBox="0 0 44 44" fill="none" stroke="#13a04a" stroke-width="3" stroke-linecap="round">
            <path d="M22 6c-4-3-11-1-11 5-5 1-6 8-2 11-3 4 0 10 5 10 2 5 8 6 8 1z"/>
            <path d="M22 6c4-3 11-1 11 5 5 1 6 8 2 11 3 4 0 10-5 10-2 5-8 6-8 1z"/>
            <line x1="22" y1="6" x2="22" y2="33"/><path d="M15 16c3 0 4 2 4 4M29 16c-3 0-4 2-4 4M14 25h5M30 25h-5"/>
          </svg>
        </span>
        <span class="benefit__label">Anxiety<br>Support</span>
      </li>
      <li class="benefit">
        <span class="benefit__icon">
          <svg width="44" height="44" viewBox="0 0 44 44">
            <path d="M24 6a16 16 0 1 0 14 22A13 13 0 0 1 24 6z" fill="#13a04a"/>
            <path d="M31 9l1.5 3.5L36 14l-3.5 1.5L31 19l-1.5-3.5L26 14l3.5-1.5z" fill="#13a04a"/>
          </svg>
        </span>
        <span class="benefit__label">Sleep<br>Support</span>
      </li>
    </ul>

    <div class="strength">
      <div class="strength__dose">3000<small>MG</small></div>
      <div class="strength__cbd">CBD</div>
    </div>

    <svg class="count-tab" viewBox="0 0 300 100" aria-hidden="true">
      <defs>
        <linearGradient id="silverTab" x1="0" y1="0" x2="1" y2="1">
          <stop offset="0" stop-color="#c3c8cd"/><stop offset=".5" stop-color="#f4f5f6"/><stop offset="1" stop-color="#cdd1d5"/>
        </linearGradient>
      </defs>
      <polygon points="40,0 300,0 300,100 0,100" fill="url(#silverTab)"/>
    </svg>
    <div class="count">
      <svg width="50" height="40" viewBox="0 0 50 40" aria-hidden="true">
        <rect x="4" y="6" width="14" height="30" rx="7" transform="rotate(15 11 21)" fill="#16239a"/>
        <rect x="26" y="6" width="14" height="30" rx="7" transform="rotate(15 33 21)" fill="#16239a"/>
      </svg>
      <span class="count__num">30<small>CAPSULES</small></span>
    </div>

    <div class="band-bottom"></div>
  </section>

</main>
</body>
</html>
```